Profesional personal website needs design and business card

I need a business card with my professional name as a logo "Dorian Vitality" for my business. I am a Wellness Coach, consultant and trainer. So it should be professional, wellness oriented and modern.

Target Market(s)

Private clients, governments, corporations. Luxury and high market.

Industry/Entity Type

Health And Wellness

Contact Information for Business Card

Dorian Vitality should be the logo

Colors

Designer to choose colors to be used in the design.

Requirements
Must have
• Dorian Vitality
• Name: Tomás Lirandel
• Wellness Coach, Consultant & Trainer.
• Website: www.dorianvitality-example.com
• Phone:
• Spain (+34) 612 480 317
• (USA) +1 (555) 610 4829
Nice to have
• The most important is the design of "Dorian Vitality", as this is going to be my personal brand logo. It should be professional, wellness, high end and actual.
Should not have
• no golds, no baroque style..

```html
<!DOCTYPE html>
<html lang="en">
<head>
<meta charset="utf-8">
<title>Dorian Vitality — Business Card</title>
<link href="https://fonts.googleapis.com/css2?family=Montserrat:wght@300;400;500;700&display=swap" rel="stylesheet">
<style>
  :root {
    --stage: #d6d5d8;
    --charcoal: #252428;
    --charcoal-soft: #2f2f34;
    --leaf: #8cc53f;
    --leaf-light: #b3d855;
    --paper-white: #e6e6e7;
    --ink-white: #ffffff;
  }
  * { margin: 0; padding: 0; box-sizing: border-box; }
  html, body {
    width: 1200px; height: 1200px; overflow: hidden;
    background: var(--stage);
    font-family: "Montserrat", sans-serif;
  }
  .stage {
    width: 1200px; height: 1200px;
    display: flex; flex-direction: column;
    align-items: center; justify-content: center; gap: 40px;
  }
  .card {
    position: relative;
    width: 840px; height: 538px;
    overflow: hidden;
    box-shadow: 0 10px 30px rgba(0,0,0,0.18);
  }
  /* Back: brand side */
  .card-back {
    background: var(--charcoal);
    display: flex; align-items: center; justify-content: center;
  }
  .brand-name {
    color: var(--leaf);
    font-weight: 500;
    font-size: 66px;
    letter-spacing: 1px;
  }
  /* Front: contact side */
  .card-front { background: var(--leaf); color: var(--ink-white); }
  .holder-name {
    position: absolute; left: 53px; top: 50px;
    font-size: 35px; letter-spacing: 4px; line-height: 1;
  }
  .holder-name .first { font-weight: 700; }
  .holder-name .last { font-weight: 300; }
  .holder-role {
    position: absolute; left: 53px; top: 92px;
    font-size: 13.5px; font-weight: 500; letter-spacing: 2.4px;
  }
  .divider {
    position: absolute; left: 53px; top: 126px;
    width: 246px; height: 3px; background: var(--charcoal);
  }
  .divider::before {
    content: ""; position: absolute; left: 0; top: -1px;
    width: 42px; height: 5px; background: var(--charcoal);
  }
  .contact-line {
    position: absolute; left: 53px;
    display: flex; align-items: center; gap: 20px;
    font-weight: 400;
  }
  .contact-web { top: 150px; font-size: 22px; letter-spacing: 1.2px; }
  .contact-phone { top: 446px; font-size: 20px; letter-spacing: 1px; line-height: 1.25; }
  .contact-line svg { flex: none; }
  .edge-panel {
    position: absolute; right: 0; top: 0;
    width: 200px; height: 538px;
    background: linear-gradient(180deg, var(--leaf) 0%, var(--leaf-light) 40%, var(--charcoal-soft) 100%);
  }
</style>
</head>
<body>
<main class="stage">

  <section class="card card-back" aria-label="Card back with brand name">
    <span class="brand-name">Dorian Vitality</span>
  </section>

  <section class="card card-front" aria-label="Card front with contact details">
    <div class="edge-panel" role="img" aria-label="Decorative angled bands in charcoal, white and light green"></div>

    <h1 class="holder-name"><span class="first">TOMÁS</span> <span class="last">LIRANDEL</span></h1>
    <p class="holder-role">Wellness Coach - Consultant &amp; Trainer</p>
    <div class="divider"></div>

    <p class="contact-line contact-web">
      <svg width="16" height="22" viewBox="0 0 16 22" aria-hidden="true">
        <polygon fill="var(--ink-white)" points="1,1 1,17 5,13 8,20 11,19 8,12 14,12"/>
      </svg>
      <span>www.dorianvitality-example.com</span>
    </p>

    <div class="contact-line contact-phone">
      <svg width="20" height="22" viewBox="0 0 24 24" aria-hidden="true">
        <path fill="var(--ink-white)" d="M6.6 10.8c1.4 2.8 3.8 5.1 6.6 6.6l2.2-2.2c.3-.3.7-.4 1-.2 1.1.4 2.3.6 3.6.6.6 0 1 .4 1 1V20c0 .6-.4 1-1 1C10.6 21 3 13.4 3 4c0-.6.4-1 1-1h3.5c.6 0 1 .4 1 1 0 1.3.2 2.5.6 3.6.1.3 0 .7-.2 1z"/>
      </svg>
      <p>SPAIN(+34) 612 480 317<br>USA&nbsp;&nbsp;+1 (555) 610 4829</p>
    </div>
  </section>

</main>
</body>
</html>
```